Kor'v Meridell Travel

We need a sleek, professional, inviting card to elicit global travel for the experienced and professional traveler. Royal blue, black and silver. (perhaps the wording could be silver with black shadow?-get creative) Maybe a watermark on the front and the full raised logo on the back.
We want a stylish and modern card, but professional.

```html
<!DOCTYPE html>
<html lang="en">
<head>
<meta charset="utf-8">
<title>Kor'v Meridell Travel – Business Card</title>
<link href="https://fonts.googleapis.com/css2?family=Open+Sans:wght@400;700;800&display=swap" rel="stylesheet">
<style>
  :root {
    --backdrop: #2a2a2c;
    --card: #1b1b1c;
    --brand-blue: #27a4e2;
    --brand-green: #8dc63f;
    --text-light: #d4d4d4;
    --text-muted: #a9a9a9;
  }
  * { box-sizing: border-box; margin: 0; padding: 0; }
  html, body {
    width: 1200px; height: 900px; overflow: hidden;
    background: var(--backdrop);
    font-family: "Open Sans", Arial, sans-serif;
  }
  .canvas {
    width: 1200px; height: 900px;
    display: flex; align-items: center; justify-content: center;
  }
  .card {
    position: relative;
    width: 980px; height: 560px;
    background: var(--card);
    box-shadow: 0 18px 40px rgba(0,0,0,.45);
    display: flex; align-items: center;
  }
  .brand {
    width: 470px;
    display: flex; flex-direction: column; align-items: center;
    padding-left: 40px;
  }
  .brand-mark {
    display: flex; align-items: center; gap: 14px;
  }
  .brand-dot {
    width: 22px; height: 22px; border-radius: 50%;
    background: var(--brand-green);
  }
  .brand-name {
    color: var(--brand-blue);
    font-weight: 700;
    font-size: 34px;
    letter-spacing: 1px;
    text-transform: uppercase;
    line-height: 1.15;
    text-align: center;
  }
  .brand-rule {
    margin-top: 18px;
    width: 360px; height: 2px;
    background: var(--brand-green);
  }
  .divider {
    width: 2px; height: 230px;
    background: var(--brand-blue);
    margin: 0 44px 0 30px;
  }
  .contact { color: var(--text-light); }
  .contact-name {
    color: var(--brand-blue);
    font-weight: 800;
    font-size: 30px;
    text-transform: uppercase;
    letter-spacing: .5px;
  }
  .contact-title {
    color: var(--text-muted);
    font-size: 19px;
    margin-bottom: 14px;
  }
  .contact-address { font-size: 19px; line-height: 1.35; margin-bottom: 12px; }
  .contact-list { list-style: none; font-size: 19px; line-height: 1.45; }
  .contact-list li { display: flex; align-items: center; gap: 10px; }
  .contact-list svg { width: 16px; height: 16px; fill: var(--brand-green); flex: none; }
</style>
</head>
<body>
<main class="canvas">
  <article class="card">
    <section class="brand">
      <div class="brand-mark">
        <span class="brand-dot"></span>
        <span class="brand-name">Kor'v Meridell<br>Travel</span>
      </div>
      <div class="brand-rule"></div>
    </section>

    <div class="divider"></div>

    <section class="contact">
      <h1 class="contact-name">Dale Corwin</h1>
      <p class="contact-title">President</p>
      <p class="contact-address">18340 Harbor Crest Way<br>Lindmoor CA 90417</p>
      <ul class="contact-list">
        <li>
          <svg viewBox="0 0 24 24" aria-hidden="true"><path d="M6.6 10.8a15.1 15.1 0 0 0 6.6 6.6l2.2-2.2a1 1 0 0 1 1-.25 11.4 11.4 0 0 0 3.6.57 1 1 0 0 1 1 1V20a1 1 0 0 1-1 1A17 17 0 0 1 3 4a1 1 0 0 1 1-1h3.5a1 1 0 0 1 1 1c0 1.25.2 2.45.57 3.57a1 1 0 0 1-.25 1z"/></svg>
          555-214-0387
        </li>
        <li>
          <svg viewBox="0 0 24 24" aria-hidden="true"><path d="M2 5h20v14H2z M2 5l10 8 10-8" stroke="#1b1b1c" stroke-width="1.5"/></svg>
          info@korvmeridell.com
        </li>
        <li>
          <svg viewBox="0 0 24 24" aria-hidden="true"><circle cx="12" cy="12" r="10"/><path d="M2 12h20M12 2c3 3 3 17 0 20M12 2c-3 3-3 17 0 20" stroke="#1b1b1c" stroke-width="1.5" fill="none"/></svg>
          www.korvmeridell.com
        </li>
      </ul>
    </section>
  </article>
</main>
</body>
</html>
```